Design a modern, classy & professional business card for an online real estate agency, specializing in medium-luxury properties in Thailand and later in Singapore and UK.

Possible design ideas so far: (not essential)

- curved corner(s) to the card, white on front & turquoise on back or visa versa.

- front of card - clear and simple, company name in metallic grey/monochrome, logo graphic & company name on front in spot UV or embossed/debossed effect.

- back of card - large, close-cropped, 'ghost' patterns of the C-shaped curves of logo, or company name repeated on back of card in spot UV.

Target Market(s)

- young to middle-aged professionals mainly (but ideally should design should suit all)

- UK, US,EU,AUS & ASIAN mainly (but ideally should design should suit all countries)

Industry/Entity Type

Real Estate

Requirements
Must have
• THEME:
- Luxurious & Modern
- Clean & striking
- Unique & creative

INFO:
- Logo & company name on front
- Contact details on back:

Tobias Hennlund
Managing Director

www.velmontestates.asia
www.velmontestates.co.uk

Tel: 083-274-6159
email: tobias@velmontestates.asia

(contact details can be displayed in any order as suites design.)

Nice to have
• - curved corner(s) to the card, white on front & turquoise on back or visa versa.

Should not have
• - No generic images of properties, palm trees/coconut trees etc.

- No other other bold colors, except for main turquoise, grey, metallic white & black theme.

- No obvious business card templates

```html
<!DOCTYPE html>
<html lang="en">
<head>
<meta charset="utf-8">
<title>Velmont Estates — Business Card</title>
<link rel="stylesheet" href="https://fonts.googleapis.com/css2?family=Exo+2:wght@400;600;800&display=swap">
<style>
  :root {
    --stage: #ecebe8;
    --card-white: #ffffff;
    --card-grey: #6d6e70;
    --turquoise: #1fc3c4;
    --ink-white: #ffffff;
    --line-white: rgba(255,255,255,0.95);
  }
  * { box-sizing: border-box; margin: 0; padding: 0; }
  html, body {
    width: 1200px; height: 1050px; overflow: hidden;
    background: var(--stage);
    font-family: "Exo 2", sans-serif;
  }
  .card {
    position: absolute; left: 325px; top: 45px;
    width: 550px; height: 960px;
    background: var(--card-grey);
    overflow: hidden;
    box-shadow: 0 10px 30px rgba(0,0,0,0.18);
  }
  .card__header {
    position: absolute; left: 0; top: 0; width: 100%; height: 300px;
    background: var(--card-white);
  }
  .card__rule-top {
    position: absolute; left: 0; top: 18px; width: 100%; height: 8px;
    background: var(--turquoise);
  }
  .card__rule-header {
    position: absolute; left: 0; top: 292px; width: 100%; height: 8px;
    background: var(--turquoise);
  }
  .brand {
    position: absolute; left: 0; top: 90px; width: 100%;
    display: flex; flex-direction: column; align-items: center; gap: 16px;
  }
  .brand__mark {
    width: 62px; height: 62px; background: var(--turquoise);
  }
  .brand__name {
    font-weight: 600; font-size: 38px; color: var(--card-grey);
    letter-spacing: 1px;
  }
  .connectors { position: absolute; left: 0; top: 0; width: 550px; height: 960px; }
  .namebox {
    position: absolute; left: 190px; top: 310px; width: 340px; height: 100px;
    background: var(--card-white);
    padding: 20px 20px 0;
    color: var(--turquoise);
    white-space: nowrap;
  }
  .namebox__name {
    font-weight: 800; font-size: 25px; letter-spacing: 0.5px; text-transform: uppercase;
    line-height: 1.1;
  }
  .namebox__title { font-weight: 400; font-size: 19px; margin-top: 8px; line-height: 1.1; }
  .contact {
    position: absolute; width: 350px; height: 90px;
    border: 2px solid var(--line-white);
    color: var(--ink-white);
    text-align: center;
    padding-top: 14px;
  }
  .contact__label {
    font-weight: 800; font-size: 24px; letter-spacing: 1px; text-transform: uppercase;
    line-height: 1.2;
  }
  .contact__value { font-weight: 400; font-size: 19px; margin-top: 4px; letter-spacing: 0.5px; line-height: 1.25; }
  .contact--phone { left: 170px; top: 450px; }
  .contact--email { left: 130px; top: 570px; }
  .contact--web { left: 90px; top: 690px; height: 116px; }
  .address-band {
    position: absolute; left: 0; top: 840px; width: 100%; height: 88px;
    background: var(--turquoise);
    color: var(--ink-white);
    display: flex; align-items: center; justify-content: center;
    font-weight: 400; font-size: 24px; letter-spacing: 1px;
  }
</style>
</head>
<body>
  <article class="card">
    <div class="card__header"></div>
    <div class="card__rule-top"></div>
    <div class="card__rule-header"></div>

    <div class="brand">
      <div class="brand__mark"></div>
      <div class="brand__name">Velmont Estates</div>
    </div>

    <svg class="connectors" viewBox="0 0 550 960" aria-hidden="true">
      <g stroke="#ffffff" stroke-width="2" fill="none">
        <line x1="60" y1="330" x2="60" y2="748"/>
        <line x1="60" y1="330" x2="190" y2="330"/>
        <line x1="60" y1="495" x2="170" y2="495"/>
        <line x1="60" y1="615" x2="130" y2="615"/>
        <line x1="60" y1="748" x2="90" y2="748"/>
      </g>
    </svg>

    <div class="namebox">
      <div class="namebox__name">Tobias Hennlund</div>
      <div class="namebox__title">Managing Director</div>
    </div>

    <div class="contact contact--phone">
      <div class="contact__label">Phone</div>
      <div class="contact__value">083-274-6159</div>
    </div>
    <div class="contact contact--email">
      <div class="contact__label">Email</div>
      <div class="contact__value">tobias@velmontestates.asia</div>
    </div>
    <div class="contact contact--web">
      <div class="contact__label">Website</div>
      <div class="contact__value">www.velmontestates.asia<br>www.velmontestates.co.uk</div>
    </div>

    <div class="address-band">041.12th floor,Quay Harbour Road BKK</div>
  </article>
</body>
</html>
```